Agriculture Business Card

I want to use my existing logo and use my tagline of "Don't Guess...Soil Test" on the card. Looking for a double sided card that will really get peoples attention.
Contact Info:
Marlow Field Crop Edge
Calvin Brusk
2917 K Lane
Larkin, NE 68593
402-555-0193
calvin.r.brusk@fieldmailbox.net

```html
<!DOCTYPE html>
<html lang="en">
<head>
<meta charset="utf-8">
<title>Marlow Field Crop Edge – Business Card</title>
<link href="https://fonts.googleapis.com/css2?family=Montserrat:wght@400;500;800&display=swap" rel="stylesheet">
<style>
  :root {
    --page-bg: #d9dbdd;
    --card-white: #ffffff;
    --card-black: #151515;
    --pattern-tone: #2a2a2a;
    --name-green: #2fb34a;
    --text-dark: #1d1d1d;
    --text-light: #f2f2f2;
    --brand-brown: #9a5a3c;
    --logo-gold: #f4b21a;
  }
  * { margin: 0; padding: 0; box-sizing: border-box; }
  html, body {
    width: 1200px; height: 900px; overflow: hidden;
    background: var(--page-bg);
    font-family: "Montserrat", Arial, sans-serif;
  }
  .sheet {
    width: 1200px; height: 900px;
    display: flex; flex-direction: column;
    align-items: center; justify-content: center; gap: 40px;
  }
  .card {
    width: 700px; height: 400px;
    border-radius: 26px;
    position: relative;
    overflow: hidden;
    box-shadow: 0 10px 30px rgba(0,0,0,0.25);
  }
  .card-front { background: var(--card-white); }
  .card-back { background: var(--card-black); }

  .contact-block {
    position: absolute; left: 56px; top: 120px;
    color: var(--text-dark);
  }
  .person-name {
    font-weight: 800; font-size: 34px; color: var(--name-green);
    text-transform: uppercase; letter-spacing: 0.5px;
    margin-bottom: 14px;
  }
  .address { font-size: 17px; line-height: 1.35; margin-bottom: 14px; }
  .contact-line {
    display: flex; align-items: center; gap: 8px;
    font-size: 17px; line-height: 1.5;
  }
  .contact-line svg { width: 14px; height: 14px; flex: none; }

  .brand-mark {
    position: absolute; right: 44px; top: 210px;
    display: flex; align-items: center; gap: 12px;
    width: 230px;
  }
  .brand-dot {
    width: 34px; height: 34px; border-radius: 50%;
    background: var(--logo-gold); flex: none;
  }
  .brand-name {
    font-weight: 800; font-size: 24px; line-height: 1.15;
    color: var(--brand-brown);
  }

  .back-pattern {
    position: absolute; inset: 0;
    background: linear-gradient(135deg, var(--pattern-tone), var(--card-black));
  }
  .back-brand {
    position: absolute; right: 40px; top: 34px;
    display: flex; align-items: center; gap: 8px;
  }
  .back-brand .brand-dot { width: 18px; height: 18px; }
  .back-brand .brand-name { font-size: 15px; color: var(--logo-gold); }

  .tagline {
    position: absolute; left: 0; right: 0; top: 50%;
    transform: translateY(-50%);
    text-align: center;
    font-weight: 800; font-size: 40px; letter-spacing: 1px;
    color: var(--text-light);
    text-transform: uppercase;
  }
  .tagline-rule {
    display: block; width: 120px; height: 4px; margin: 18px auto 0;
    background: var(--logo-gold); border-radius: 2px;
  }
</style>
</head>
<body>
<main class="sheet">
  <section class="card card-front">
    <div class="contact-block">
      <h1 class="person-name">Calvin Brusk</h1>
      <p class="address">2917 K Lane<br>Larkin, NE 68593</p>
      <p class="contact-line">
        <svg viewBox="0 0 24 24" aria-hidden="true"><path fill="#2fb34a" d="M6.6 10.8a15.1 15.1 0 0 0 6.6 6.6l2.2-2.2c.3-.3.7-.4 1-.2 1.1.4 2.3.6 3.6.6.6 0 1 .4 1 1V20c0 .6-.4 1-1 1A17 17 0 0 1 3 4c0-.6.4-1 1-1h3.5c.6 0 1 .4 1 1 0 1.3.2 2.5.6 3.6.1.3 0 .7-.2 1z"/></svg>
        402-555-0193
      </p>
      <p class="contact-line">
        <svg viewBox="0 0 24 24" aria-hidden="true"><rect x="2" y="5" width="20" height="14" rx="2" fill="#2fb34a"/><path d="M3 6l9 7 9-7" fill="none" stroke="#fff" stroke-width="2"/></svg>
        calvin.r.brusk@fieldmailbox.net
      </p>
    </div>
    <div class="brand-mark">
      <span class="brand-dot"></span>
      <span class="brand-name">Marlow Field Crop Edge</span>
    </div>
  </section>

  <section class="card card-back">
    <div class="back-pattern" role="img" aria-label="Repeating tone-on-tone pattern of the brand symbol across the dark card back"></div>
    <div class="back-brand">
      <span class="brand-dot"></span>
      <span class="brand-name">Marlow Field Crop Edge</span>
    </div>
    <p class="tagline">Don't Guess...Soil Test<span class="tagline-rule"></span></p>
  </section>
</main>
</body>
</html>
```